Vantro cards

I am in the auto motive, transportation business I would like a business card that is Something cool, modern edgy, having to do with car culture. I offer towing service for high and exotic cars. I also provide towing for collisions and car accidents. I offer open and enclosed transport nationwide.

Target Market(s)

Car culture people high end auto collectors

Industry/Entity Type

Towing car carrier

Contact Information for Business Card

My company colors black yellow and silver

Font styles to use
Serif

```html
<!DOCTYPE html>
<html lang="en">
<head>
<meta charset="utf-8">
<title>Vantro Transportation – Business Cards</title>
<link rel="stylesheet" href="https://fonts.googleapis.com/css2?family=Arimo:wght@400;700&family=Roboto+Slab:wght@700;800&display=swap">
<style>
  :root {
    --stage: #2a2a2a;
    --card-black: #1d1d1d;
    --pattern-dark: #161616;
    --pattern-mid: #2b2b2b;
    --brand-yellow: #f8e05a;
    --brand-silver: #bdbdbd;
    --text-white: #f2f2f2;
  }
  * { margin: 0; padding: 0; box-sizing: border-box; }
  html, body {
    width: 1200px; height: 900px; overflow: hidden;
    background: var(--stage);
    font-family: "Arimo", Arial, sans-serif;
  }
  .canvas { position: relative; width: 1200px; height: 900px; }

  .card {
    position: absolute; width: 700px; height: 400px;
    border-radius: 22px; overflow: hidden;
    background: var(--card-black);
    box-shadow: 0 18px 40px rgba(0,0,0,.45);
  }

  .brand-mark {
    font-family: "Roboto Slab", Georgia, serif;
    font-weight: 800; text-transform: uppercase; text-align: center;
    line-height: 1;
  }
  .brand-mark small { display: block; letter-spacing: 2px; }

  /* back side */
  .card-back { left: 80px; top: 40px; }
  .back-pattern {
    position: absolute; inset: 0;
    background: radial-gradient(circle at 70% 40%, var(--pattern-mid), var(--pattern-dark) 75%);
  }
  .back-brand {
    position: absolute; left: 380px; top: 120px; width: 240px;
    font-size: 40px; color: var(--brand-yellow);
  }
  .back-brand small { font-size: 15px; margin-top: 8px; }

  /* front side */
  .card-front { left: 420px; top: 460px; }
  .front-wave { position: absolute; inset: 0; }
  .contact-block { position: absolute; left: 52px; top: 46px; color: var(--text-white); }
  .name-bar {
    position: absolute; left: -24px; top: 8px; width: 10px; height: 46px;
    background: var(--brand-yellow);
  }
  .person-name { font-weight: 700; font-size: 26px; color: var(--brand-yellow); }
  .person-role { font-size: 17px; margin-top: 2px; }
  .address { font-size: 17px; line-height: 1.3; margin-top: 24px; margin-left: 14px; }
  .contact-list { list-style: none; margin-top: 18px; margin-left: 14px; }
  .contact-list li {
    display: flex; align-items: center; gap: 12px;
    font-size: 18px; line-height: 1.5;
  }
  .contact-list svg { width: 16px; height: 16px; flex: none; }
  .front-brand {
    position: absolute; left: 405px; top: 80px; width: 275px;
    font-size: 58px; color: var(--brand-silver);
  }
  .front-brand small { font-size: 20px; margin-top: 10px; }
</style>
</head>
<body>
<main class="canvas">

  <section class="card card-back">
    <div class="back-pattern" role="img" aria-label="Tonal repeat pattern of the company badge on black"></div>
    <div class="brand-mark back-brand">Vantro<small>Transportation</small></div>
  </section>

  <section class="card card-front">
    <svg class="front-wave" viewBox="0 0 700 400" preserveAspectRatio="none" aria-hidden="true">
      <path d="M0,298 C180,322 420,318 560,290 C620,278 665,262 700,250 L700,400 L0,400 Z" fill="var(--brand-silver)"/>
      <path d="M0,318 C185,344 430,336 570,306 C628,293 668,278 700,268 L700,400 L0,400 Z" fill="var(--brand-yellow)"/>
    </svg>

    <div class="contact-block">
      <span class="name-bar"></span>
      <h1 class="person-name">Marek Doruzian</h1>
      <p class="person-role">Owner Operator</p>
      <p class="address">2187 Linden ave #4<br>Valley Glen CA 91401</p>
      <ul class="contact-list">
        <li>
          <svg viewBox="0 0 16 16"><path d="M3 1.5l3 .5 1 3.5-2 1.3a9 9 0 0 0 4.2 4.2l1.3-2 3.5 1 .5 3c-.3.8-1.3 1.5-2.3 1.5C6.5 14.5 1.5 9.5 1.5 3.8c0-1 .7-2 1.5-2.3z" fill="var(--brand-yellow)"/></svg>
          555-014-2290
        </li>
        <li>
          <svg viewBox="0 0 16 16"><rect x="1" y="3" width="14" height="10" rx="1" fill="var(--brand-yellow)"/><path d="M1.5 3.8L8 9l6.5-5.2" stroke="var(--card-black)" stroke-width="1.4" fill="none"/></svg>
          Vantrotowers@mailbox.com
        </li>
        <li>
          <svg viewBox="0 0 16 16"><rect x="2" y="2" width="12" height="12" rx="2" stroke="var(--brand-yellow)" stroke-width="1.8" fill="none"/></svg>
          @Mr_Haul_It_All
        </li>
      </ul>
    </div>

    <div class="brand-mark front-brand">Vantro<small>Transportation</small></div>
  </section>

</main>
</body>
</html>
```